Corvane Capital Business Cards

These are professional business cards that are for my family office.
Put fake emails and phone numbers as of now until I finalize those components. This family office controls my families investments, assets, and future. The cards should be professional.
..
.
.
.
I just uploaded another variation of a logo I would like to see as a business card to I am inbeteen which logo to use

Target Market(s)

business

Industry/Entity Type

business

Contact Information for Business Card

Professional, wealth related, finance related.

Requirements
Must have
• Logo

```html
<!DOCTYPE html>
<html lang="en">
<head>
<meta charset="utf-8">
<title>Corvane Capital Business Cards</title>
<link href="https://fonts.googleapis.com/css2?family=Cinzel:wght@600&family=Montserrat:wght@400&display=swap" rel="stylesheet">
<style>
  :root {
    --page: #e6e7ea;
    --navy: #141b2a;
    --navy-soft: #1d2638;
    --ink: #1a2233;
    --grey: #5d6068;
    --paper: #ffffff;
    --accent: #b8c6e6;
  }
  * { margin: 0; padding: 0; box-sizing: border-box; }
  html, body { width: 1200px; height: 915px; overflow: hidden; background: var(--page); }
  .canvas { position: relative; width: 1200px; height: 915px; }
  .card {
    position: absolute; left: 250px; width: 700px; height: 400px;
    border-radius: 22px; overflow: hidden;
    box-shadow: 0 6px 18px rgba(0,0,0,.18);
  }
  .card--back { top: 38px; background: var(--navy); }
  .card--front { top: 477px; background: var(--paper); }

  .pattern-area {
    position: absolute; inset: 0;
    background: linear-gradient(125deg, var(--navy) 0%, var(--navy-soft) 60%, #2a3a5c 100%);
  }
  .back-brand {
    position: absolute; right: 70px; bottom: 120px;
    display: flex; align-items: center; gap: 12px;
  }
  .back-brand .dot {
    width: 40px; height: 40px; border: 2px solid var(--paper); border-radius: 50%;
  }
  .back-brand .name {
    font-family: "Cinzel", serif; font-weight: 600; font-size: 20px; color: var(--paper);
    letter-spacing: 1px;
  }

  .front-brand {
    position: absolute; right: 48px; top: 46px;
    font-family: "Cinzel", serif; font-weight: 600; font-size: 38px; color: var(--ink);
    letter-spacing: 1px;
  }
  .marker {
    position: absolute; left: 0; top: 132px; width: 22px; height: 34px; background: var(--navy);
  }
  .person { position: absolute; left: 42px; top: 118px; }
  .person .name {
    font-family: "Cinzel", serif; font-weight: 600; font-size: 25px; color: var(--ink); line-height: 1.1;
  }
  .person .role {
    font-family: "Montserrat", sans-serif; font-size: 15px; color: var(--grey); margin-top: 4px;
  }
  .contact {
    position: absolute; left: 42px; top: 224px;
    font-family: "Montserrat", sans-serif; font-size: 15px; color: var(--grey); line-height: 1.45;
  }
  .contact .address { margin-bottom: 12px; }
  .contact .line { display: flex; align-items: center; gap: 8px; }
  .contact svg { width: 13px; height: 13px; fill: var(--ink); flex: none; }
</style>
</head>
<body>
<div class="canvas">

  <section class="card card--back">
    <div class="pattern-area" role="img" aria-label="Repeating monogram pattern across the dark card back"></div>
    <div class="back-brand">
      <span class="dot"></span>
      <span class="name">Corvane Capital</span>
    </div>
  </section>

  <section class="card card--front">
    <div class="front-brand">Corvane Capital</div>
    <div class="marker"></div>
    <div class="person">
      <div class="name">Daniel Reyes</div>
      <div class="role">CEO/Founder</div>
    </div>
    <div class="contact">
      <div class="address">4820 Linden Ridge Rd Suite 200<br>Fairmont, CA 90210</div>
      <div class="line">
        <svg viewBox="0 0 16 16" aria-hidden="true"><path d="M3 1h3l1.5 4-2 1.3a9 9 0 0 0 4.2 4.2L11 8.5l4 1.5v3a2 2 0 0 1-2 2A12 12 0 0 1 1 3a2 2 0 0 1 2-2z"/></svg>
        <span>(555) 014-2736</span>
      </div>
      <div class="line">
        <svg viewBox="0 0 16 16" aria-hidden="true"><path d="M1 3h14v10H1zM2.5 4.5 8 9l5.5-4.5v-.2h-11z" fill-rule="evenodd"/></svg>
        <span>DanielR@corvanecapital.com</span>
      </div>
      <div class="line">
        <svg viewBox="0 0 16 16" aria-hidden="true"><circle cx="8" cy="8" r="7"/></svg>
        <span>www.corvanecapital.com</span>
      </div>
    </div>
  </section>

</div>
</body>
</html>
```